Help our Sugar Loom find our winning design! We're looking for a business card....

We’re a Sugar Loom in NY specializing in custom-made cakes and unique desserts.
Our cakes combine flavor and art, each designed to match customer’s special event and theme.
We’d like a unique business card with a clean design that will combine French chic and artistic look & feel.
We’d like to differentiate ourselves from standard bakeries, please don’t offer cupcake images :-)
Our logo is peach-pink and brown and we’d love to use these colors ( . Another color that can be added is gold - or feel free to suggest!

Target Market(s)

Women, ages 25-55

Industry/Entity Type

Boutique

Contact Information for Business Card

Text on card:
Logo
Sugar Loom by Dana Welch

www.sugarloomsweets.com
hello@sugarloom.com
(516) 555-0147
F – sugarloomnyc
IG - sugarloom_ny

Font styles to use
Sans Serif
Script

Requirements
Must have
• Logo
• Clean look
• French chic and artistic look & feel.
Nice to have
• Damask pattern
Should not have
• Cupcake images

```html
<!DOCTYPE html>
<html lang="en">
<head>
<meta charset="utf-8">
<title>Sugar Loom – Business Card</title>
<link href="https://fonts.googleapis.com/css2?family=Great+Vibes&family=Open+Sans:wght@400;600&display=swap" rel="stylesheet">
<style>
  :root {
    --backdrop: #b4b4b4;
    --card-white: #ffffff;
    --blush: #f6e6e4;
    --peach-pink: #dba49c;
    --peach-soft: #efcfca;
    --cocoa: #2a1517;
    --ink: #2b2224;
    --cream-text: #f4ecea;
  }
  * { margin: 0; padding: 0; box-sizing: border-box; }
  html, body { width: 1200px; height: 852px; overflow: hidden; }
  body {
    background: var(--backdrop);
    position: relative;
    font-family: "Open Sans", Arial, sans-serif;
    color: var(--ink);
  }
  .card {
    position: absolute;
    width: 480px;
    height: 274px;
    border-radius: 22px;
    overflow: hidden;
    background: var(--card-white);
  }
  .card-front { left: 150px; top: 110px; }
  .card-back {
    left: 570px; top: 460px;
    background: linear-gradient(180deg, var(--card-white) 0%, var(--card-white) 45%, var(--blush) 100%);
  }

  .brand {
    position: absolute;
    display: flex;
    flex-direction: column;
    align-items: center;
  }
  .brand-ornament {
    border-radius: 50%;
    background: radial-gradient(ellipse at center, rgba(219,164,156,0.35) 0%, rgba(219,164,156,0.12) 60%, rgba(219,164,156,0) 100%);
  }
  .brand-name {
    font-family: "Great Vibes", cursive;
    color: var(--ink);
    line-height: 1;
    white-space: nowrap;
  }
  .card-front .brand { left: 90px; top: 50px; width: 300px; }
  .card-front .brand-ornament { width: 300px; height: 110px; }
  .card-front .brand-name { font-size: 50px; margin-top: -72px; }

  .card-back .brand { left: 24px; top: 26px; width: 220px; }
  .card-back .brand-ornament { width: 220px; height: 80px; }
  .card-back .brand-name { font-size: 38px; margin-top: -54px; }

  .wave { position: absolute; inset: 0; width: 480px; height: 274px; }

  .contact-list {
    position: absolute;
    left: 30px; top: 138px;
    list-style: none;
    font-size: 12.5px;
    line-height: 21px;
    color: var(--ink);
  }
  .contact-list li { display: flex; align-items: center; gap: 8px; }
  .contact-icon { width: 12px; height: 12px; flex: none; }
  .social-marks { display: flex; gap: 3px; }
  .social-mark { width: 10px; height: 10px; background: var(--ink); border-radius: 2px; }

  .owner {
    position: absolute;
    right: 18px; top: 118px;
    width: 130px;
    text-align: center;
    color: var(--cream-text);
  }
  .owner-line { font-size: 12.5px; letter-spacing: 0.2px; }
  .owner-name { font-family: "Great Vibes", cursive; font-size: 29px; line-height: 1.1; white-space: nowrap; }
</style>
</head>
<body>

  <section class="card card-front" aria-label="Card front">
    <div class="brand">
      <div class="brand-ornament" role="img" aria-label="Peach-pink flourish ornament with tiered cake motif"></div>
      <span class="brand-name">Sugar Loom</span>
    </div>
  </section>

  <section class="card card-back" aria-label="Card back">
    <svg class="wave" viewBox="0 0 480 274" aria-hidden="true">
      <path d="M0 236 C110 244 200 228 255 160 C300 100 370 40 480 8 L480 274 L0 274 Z" fill="var(--peach-soft)" opacity="0.5"/>
      <path d="M0 248 C120 256 215 240 270 168 C312 110 380 48 480 16" fill="none" stroke="var(--peach-pink)" stroke-width="3"/>
      <path d="M0 259 C130 266 228 250 284 176 C325 120 390 60 480 28" fill="none" stroke="var(--peach-pink)" stroke-width="1.5" opacity="0.8"/>
      <path d="M480 22 C400 34 352 82 322 140 C292 200 236 252 140 274 L480 274 Z" fill="var(--cocoa)"/>
    </svg>

    <div class="brand">
      <div class="brand-ornament" role="img" aria-label="Peach-pink flourish ornament with tiered cake motif"></div>
      <span class="brand-name">Sugar Loom</span>
    </div>

    <ul class="contact-list">
      <li>
        <svg class="contact-icon" viewBox="0 0 12 12" aria-hidden="true"><path d="M1 4 Q6 0 11 4 L9 5.5 L8 4 H4 L3 5.5 Z M3 6 H9 L10 11 H2 Z" fill="var(--ink)"/></svg>
        <span>(516) 555-0147</span>
      </li>
      <li>
        <svg class="contact-icon" viewBox="0 0 12 12" aria-hidden="true"><rect x="0.5" y="2" width="11" height="8" fill="var(--ink)"/><path d="M0.5 2 L6 6.5 L11.5 2" fill="none" stroke="#fff" stroke-width="1"/></svg>
        <span>hello@sugarloom.com</span>
      </li>
      <li>
        <svg class="contact-icon" viewBox="0 0 12 12" aria-hidden="true"><circle cx="6" cy="6" r="5.2" fill="none" stroke="var(--ink)" stroke-width="1.2"/><ellipse cx="6" cy="6" rx="2.2" ry="5.2" fill="none" stroke="var(--ink)" stroke-width="1"/><line x1="0.8" y1="6" x2="11.2" y2="6" stroke="var(--ink)" stroke-width="1"/></svg>
        <span>www.sugarloomsweets.com</span>
      </li>
      <li>
        <span class="social-marks"><span class="social-mark"></span><span class="social-mark"></span></span>
        <span>sugarloomnyc</span>
      </li>
    </ul>

    <div class="owner">
      <p class="owner-line">Sugar Loom by</p>
      <p class="owner-name">Dana Welch</p>
    </div>
  </section>

</body>
</html>
```